High Tech Real Estate Startup needs a business card

We are developing an innovative real estate marketing product based around advanced search and virtual reality.

We talk to people, we need business cards.

Target Market(s)

The target market is technology professionals and realtors.

Contact Information for Business Card

The information to be included will include

Name
Title
Phone Number
E-mail Address
www.zelquin.com

It should use simple iconography for each one of those fields.

Font styles to use
Other font styles liked:
• Co, Jubilat, Avenir

Colors

Designer to choose colors to be used in the design.

Requirements
Must have
• Clean aesthetic,
• Good use of negative space.
• It should use our company logo, shown in the attached file. It is able to use the negative of that logo (coloured font and white background) and I have attached other acceptable accent colours in a swatch file.
Should not have
• Should not be too busy
• No extraneous text (slogans, tag lines etc)

```html
<!DOCTYPE html>
<html lang="en">
<head>
<meta charset="UTF-8">
<title>Zelquin Business Card</title>
<link rel="stylesheet" href="https://fonts.googleapis.com/css2?family=Open+Sans:wght@400;600&display=swap">
<style>
  :root {
    --backdrop: #3a3a3c;
    --card: #202022;
    --accent: #3dbdc1;
    --ink-light: #e8e8e8;
    --ink-muted: #c9c9c9;
  }
  * { margin: 0; padding: 0; box-sizing: border-box; }
  html, body {
    width: 799px;
    height: 1200px;
    overflow: hidden;
    background: var(--backdrop);
    font-family: "Open Sans", Arial, sans-serif;
  }
  .sheet {
    width: 799px;
    height: 1200px;
    display: flex;
    flex-direction: column;
  }
  .side {
    flex: 1;
    display: flex;
    align-items: center;
    justify-content: center;
  }
  .card {
    position: relative;
    width: 580px;
    height: 340px;
    border-radius: 26px;
    background: var(--card);
    box-shadow: 0 14px 30px rgba(0, 0, 0, 0.45);
  }
  .wordmark {
    color: var(--accent);
    font-weight: 600;
    letter-spacing: 4px;
  }
  .card-front .wordmark {
    position: absolute;
    inset: 0;
    display: flex;
    align-items: center;
    justify-content: center;
    font-size: 64px;
  }
  .card-back .wordmark {
    position: absolute;
    left: 46px;
    top: 104px;
    font-size: 44px;
  }
  .contact {
    position: absolute;
    left: 312px;
    top: 178px;
  }
  .contact-name {
    color: var(--accent);
    font-weight: 600;
    font-size: 22px;
    line-height: 1.1;
  }
  .contact-title {
    color: var(--ink-muted);
    font-size: 13px;
    margin-bottom: 12px;
  }
  .contact-list {
    list-style: none;
  }
  .contact-item {
    display: flex;
    align-items: center;
    gap: 9px;
    color: var(--ink-light);
    font-size: 14px;
    line-height: 22px;
  }
  .contact-icon {
    width: 16px;
    height: 16px;
    flex: none;
  }
</style>
</head>
<body>
<main class="sheet">
  <section class="side">
    <div class="card card-front">
      <div class="wordmark">ZELQUIN</div>
    </div>
  </section>
  <section class="side">
    <div class="card card-back">
      <div class="wordmark">ZELQUIN</div>
      <div class="contact">
        <p class="contact-name">John Doe Smith</p>
        <p class="contact-title">Managing Director</p>
        <ul class="contact-list">
          <li class="contact-item">
            <svg class="contact-icon" viewBox="0 0 16 16" aria-hidden="true">
              <circle cx="8" cy="8" r="8" fill="var(--accent)"/>
              <path d="M5.2 4.5l1.4-.3.8 1.9-.9.7c.4.9 1.1 1.6 2 2l.7-.9 1.9.8-.3 1.4c-3 .2-5.8-2.6-5.6-5.6z" fill="var(--card)"/>
            </svg>
            555.555.5555
          </li>
          <li class="contact-item">
            <svg class="contact-icon" viewBox="0 0 16 16" aria-hidden="true">
              <circle cx="8" cy="8" r="8" fill="var(--accent)"/>
              <rect x="4" y="5.2" width="8" height="5.6" rx="0.6" fill="var(--card)"/>
              <path d="M4.3 5.6L8 8.4l3.7-2.8" stroke="var(--accent)" stroke-width="0.8" fill="none"/>
            </svg>
            johndoe@zelquin.com
          </li>
          <li class="contact-item">
            <svg class="contact-icon" viewBox="0 0 16 16" aria-hidden="true">
              <circle cx="8" cy="8" r="8" fill="var(--accent)"/>
              <circle cx="8" cy="8" r="4" fill="none" stroke="var(--card)" stroke-width="1"/>
              <ellipse cx="8" cy="8" rx="1.7" ry="4" fill="none" stroke="var(--card)" stroke-width="0.9"/>
              <path d="M4 8h8" stroke="var(--card)" stroke-width="0.9"/>
            </svg>
            www.zelquin.com
          </li>
        </ul>
      </div>
    </div>
  </section>
</main>
</body>
</html>
```